Las Vegas Tour guide needs website of future for physical and selfguided assets

Neon Drifters is the parent site to my Las Vegas tour operation. Within this is a physical walking tour called Whispers and the Racket, the site traffic driver where I tell history with a paranormal twist. The legacy site can be seen at spookyroutewalks.com.
The Neon Drifters app has self guided tours called Desert Hop Trail/Whispers and The Racket Retold/Calloway Row Stroll. Rivano is a 3rd party tour company I have partnered with to sale self-guided tours with a scavenger hunt theme.
I like black and pink and pistachio green colors however am flexible in theme. Colors should follow Vegas 50-60s aesthetics. The “Greetings From Silver Gulch Marker” should not be considered as design inspiration. 95% of traffic is on mobile. Final design should be easy to understand guided versus self-guided option. Show cross promotion links for digital assets/physical tour. Rivano content tbd by end of week 9 Aug 2021
sites i like
nationalspiritstrolls.com
heronsandshades.com
oldportphantomtrips.net
Updates

Needs a book now at top, or floating like lorvantrips. Less busy and stay away from using photos. I have included more websites for inspiration. I would like a mashup of the two sites eerieechoplace and lorvantrips. I am unsure what some of your designs would look like on a mobile screen. Please screenshot that. https://eerieechoplace.com/ https://www.lorvantrips.com/ https://k7vrx.com/ https://bqspecters.com/ https://bluefinjaunts.com/tours/new-york-city/shades-of-pellham-corner/

Family member hospitalized need extra time to review

Target Market(s)

Tourist 25+

Industry/Entity Type

Travel. Tour guide.

Coding

Coded - Design and coding required

Number of Pages Required

5+ page

Font styles to use
Serif

Colors
00AB8E
00BBA5
67D7C9
C6EFE9
E9F9F6
59FF00
82FF00
B8FF75
E3FFCB
F4FFEA
EB3D1F
EC4F4E
F09395
F8D3D4
FCEDEE
E54698
E96AAD
F1A4CE
F9D9EA
FCEFF6

Requirements
Must have
• Cross promotion between physical tour and digital
Nice to have
• sliver button like ads as breaks between tour info
Should not have
• "Greetings from Silver Gulch Marker". no photos. no animation.

```html
<!DOCTYPE html>
<html lang="en">
<head>
<meta charset="utf-8">
<title>Neon Drifters Walking Tours</title>
<link rel="stylesheet" href="https://fonts.googleapis.com/css2?family=Playfair+Display:wght@500;600;700&family=Lora:wght@400;500;600;700&display=swap">
<style>
:root{
  --pink:#e54698;
  --pink-soft:#f1a4ce;
  --red:#eb3d1f;
  --teal:#00ab8e;
  --pistachio:#82ff00;
  --pistachio-soft:#b8ff75;
  --black:#000;
  --night:#141114;
  --ink:#1a1a1a;
  --muted:#555;
  --paper:#fcf3f7;
  --paper-2:#f9e3ee;
  --card:#fffafc;
  --white:#fff;
}
*{box-sizing:border-box;margin:0;padding:0}
html,body{width:1200px;height:3354px;overflow:hidden}
body{position:relative;font-family:"Lora",serif;color:var(--ink);background:var(--black)}
.abs{position:absolute}
.heading{font-family:"Playfair Display",serif;font-weight:600;text-align:center;position:absolute;left:0;width:1200px;white-space:nowrap}
.divider{position:absolute;left:545px;width:110px;height:2px;display:flex;gap:4px}
.divider span:first-child{flex:0 0 16px;background:var(--teal)}
.divider span:last-child{flex:1;background:var(--pink)}
.divider.light span:last-child{background:var(--white)}
.btn{position:absolute;display:flex;align-items:center;justify-content:center;font-weight:600;font-size:16px;color:var(--white);background:var(--pink);white-space:nowrap}
.btn.outline{background:transparent;color:var(--pink);border:1px solid var(--pink)}
.paper{background:radial-gradient(ellipse at 30% 40%,var(--paper),var(--paper-2))}

/* hero */
.hero{position:absolute;top:0;left:0;width:1200px;height:664px;background:linear-gradient(180deg,#1f1a1e 0%,var(--night) 60%,#0a090a 100%)}
.nav a{position:absolute;top:28px;color:var(--white);font-size:14px;font-weight:600;text-decoration:none;white-space:nowrap}
.brand-mark{position:absolute;left:538px;top:124px;width:124px;height:124px;border-radius:50%;background:var(--pink)}
.brand{position:absolute;left:0;width:1200px;top:276px;text-align:center;font-family:"Playfair Display",serif;font-size:40px;font-weight:700;color:var(--pink);white-space:nowrap}
.hero-line{font-size:38px}

/* tours */
.tours{position:absolute;top:664px;left:0;width:1200px;height:699px}
.card{position:absolute;top:140px;width:299px;height:458px;background:var(--card);box-shadow:0 1px 3px rgba(0,0,0,.08)}
.card .band{height:214px;background:var(--night);border-bottom:4px solid var(--pink)}
.card .badge{position:absolute;right:0;top:16px;height:30px;padding:0 14px;background:var(--pistachio);font-size:13px;font-weight:600;display:flex;align-items:center;white-space:nowrap}
.card h3{font-family:"Playfair Display",serif;font-size:19px;font-weight:600;text-align:center;margin-top:16px;line-height:1.2;padding:0 20px}
.card .mini{width:70px;height:2px;margin:14px auto 12px;display:flex;gap:3px}
.card .mini span:first-child{flex:0 0 14px;background:var(--teal)}
.card .mini span:last-child{flex:1;background:var(--pink)}
.card p{font-size:13.5px;line-height:25px;text-align:center;color:var(--muted);padding:0 12px}
.card .btn{top:404px;height:39px;width:113px;font-size:15px}

/* about */
.about{position:absolute;top:1363px;left:0;width:1200px;height:473px;background:var(--black);color:var(--white)}
.about p{position:absolute;left:180px;width:840px;font-size:14px;line-height:25px;text-align:center}

/* reviews */
.reviews{position:absolute;top:1836px;left:0;width:1200px;height:487px}
.review{position:absolute;top:214px;width:283px;height:172px;background:var(--white);border-radius:0 0 22px 0;box-shadow:0 4px 10px rgba(0,0,0,.07);padding:18px 20px}
.stars{color:var(--pink);font-size:12px;letter-spacing:1px}
.review p{font-size:12.5px;line-height:21px;color:#444;margin-top:10px}
.review h4{font-size:13px;font-weight:700;margin-top:14px}
.quote{position:absolute;right:22px;top:-18px;font-family:"Playfair Display",serif;font-size:90px;line-height:90px;color:var(--pink);font-weight:700}
.arrow{position:absolute;top:2117px;width:35px;height:35px;border-radius:50%;display:flex;align-items:center;justify-content:center}

/* press */
.press{position:absolute;top:2323px;left:0;width:1200px;height:380px;background:var(--black)}
.press-name{position:absolute;top:232px;font-family:"Playfair Display",serif;font-weight:700;font-size:24px;color:var(--white);text-align:center;width:150px;white-space:nowrap}

/* cta */
.cta{position:absolute;top:2703px;left:0;width:1200px;height:227px}

/* footer */
.footer{position:absolute;top:2930px;left:0;width:1200px;height:424px;background:var(--black);color:var(--white)}
.contact-box{position:absolute;top:81px;width:213px;height:157px;border:1px solid #444;text-align:center;font-size:15px}
.contact-box svg{margin-top:26px}
.contact-box .label{margin-top:14px}
.contact-box .value{margin-top:6px;font-size:14px}
.social{position:absolute;top:372px;width:36px;height:28px;background:#3a1f2d;border:1px solid #5a2f45}
</style>
</head>
<body>

<header class="hero">
  <nav class="nav">
    <a style="left:142px">Whispers And The Racket Las Vegas Walking Tour</a>
    <a style="left:505px">Desert Hop Trail</a>
    <a style="left:711px">Neon Drifters</a>
  </nav>
  <div class="btn" style="left:946px;top:21px;width:113px;height:38px">Book Now</div>
  <div class="brand-mark"></div>
  <div class="brand">Neon Drifters</div>
  <div class="heading hero-line" style="top:408px;color:var(--pink)">Whispers &amp; The Racket Las Vegas Walking Tour</div>
  <div class="heading hero-line" style="top:462px"><span style="color:var(--pistachio)">Desert Hop Trail</span>&nbsp;&nbsp;<span style="color:var(--teal)">Neon Drifters</span></div>
  <div class="btn" style="left:552px;top:526px;width:112px;height:39px">Book Now</div>
</header>

<section class="tours paper">
  <h2 class="heading" style="top:58px;font-size:38px;color:var(--teal)">Featured Tours</h2>
  <div class="divider" style="top:117px"><span></span><span></span></div>

  <article class="card" style="left:142px">
    <div class="band"></div>
    <div class="badge">45 Minute Walking Tour</div>
    <h3>Whispers &amp; The Racket Las Vegas Walking Tour</h3>
    <div class="mini"><span></span><span></span></div>
    <p>Lorem ipsum dolor sit amet, consectetuer adipiscing elit, sed diam nonummy nibh euismod tincidunt ut laoreet.</p>
    <div class="btn" style="left:28px">Book Now</div>
    <div class="btn outline" style="left:155px">Know More</div>
  </article>

  <article class="card" style="left:451px">
    <div class="band"></div>
    <div class="badge">Self Guided Tours</div>
    <h3 style="margin-top:22px">Desert Hop Trail</h3>
    <div class="mini"><span></span><span></span></div>
    <p>Lorem ipsum dolor sit amet, consectetuer adipiscing elit, sed diam nonummy nibh euismod tincidunt ut laoreet dolore mgna aliquam erat volutpat.</p>
    <div class="btn" style="left:28px">Book Now</div>
    <div class="btn outline" style="left:155px">Know More</div>
  </article>

  <article class="card" style="left:760px">
    <div class="band"></div>
    <div class="badge">Lorem Ispum Dummy</div>
    <h3 style="margin-top:22px">Neon Drifters</h3>
    <div class="mini"><span></span><span></span></div>
    <p>Lorem ipsum dolor sit amet, consectetuer adipiscing elit, sed diam nonummy nibh euismod tincidunt ut laoreet dolore mgna aliquam erat volutpat.</p>
    <div class="btn" style="left:28px">Book Now</div>
    <div class="btn outline" style="left:155px">Know More</div>
  </article>
</section>

<section class="about">
  <h2 class="heading" style="top:94px;font-size:38px;color:var(--white)">About Neon Drifters Walking Tour</h2>
  <div class="divider light" style="top:154px"><span></span><span></span></div>
  <p style="top:174px">Lorem ipsum dolor sit amet, consectetuer adipiscing elit, sed diam nonummy nibh euismod tincidunt ut laoreet dolore magna aliquam erat volutpat. Ut wisi enim ad minim veniam, quis nostrud exerci tation ullamcorper suscipit lobortis nisl ut aliquip ex ea commodo consequat. Duis autem vel eum iriure dolor in hendrerit in vulputate velit esse.</p>
  <p style="top:258px">Lorem ipsum dolor sit amet, consectetuer adipiscing elit, sed diam nonummy nibh euismod tincidunt ut laoreet dolore magna aliquam erat volutpat. Ut wisi enim ad minim veniam, quis nostrud exerci tation.</p>
  <div class="btn" style="left:515px;top:330px;width:170px;height:42px;background:var(--teal)">Contact Us Today</div>
</section>

<section class="reviews paper">
  <h2 class="heading" style="top:92px;font-size:42px;color:var(--teal)">Customer Reviews</h2>
  <div class="divider" style="top:157px;left:563px;width:74px"><span></span><span></span></div>

  <div class="review" style="left:142px"><div class="quote">”</div><div class="stars">★★★★★</div><p>“Lorem ipsum dolor sit amet, consectetur ipsum dolor sit amet, consectetur lodr adipiscing elit. Sed vel alique ellentesque justo. Mauris est tortor.”</p><h4>Jonah Pell</h4></div>
  <div class="review" style="left:459px"><div class="quote">”</div><div class="stars">★★★★★</div><p>“Lorem ipsum dolor sit amet, consectetur ipsum dolor sit amet, consectetur lodr adipiscing elit. Sed vel alique ellentesque justo. Mauris est tortor.”</p><h4>Liam AM</h4></div>
  <div class="review" style="left:776px"><div class="quote">”</div><div class="stars">★★★★★</div><p>“Lorem ipsum dolor sit amet, consectetur ipsum dolor sit amet, consectetur lodr adipiscing elit. Sed vel alique ellentesque justo. Mauris est tortor.”</p><h4>William WM</h4></div>
</section>
<div class="arrow" style="left:70px;background:var(--white);box-shadow:0 1px 4px rgba(0,0,0,.15)"><svg width="12" height="12" viewBox="0 0 12 12"><path d="M8 1 3 6l5 5" fill="none" stroke="#222" stroke-width="2"/></svg></div>
<div class="arrow" style="left:1096px;background:var(--teal)"><svg width="12" height="12" viewBox="0 0 12 12"><path d="M4 1l5 5-5 5" fill="none" stroke="#fff" stroke-width="2"/></svg></div>

<section class="press">
  <h2 class="heading" style="top:100px;font-size:42px;color:var(--white)">As Seen On</h2>
  <div class="divider light" style="top:166px;left:563px;width:74px"><span></span><span></span></div>
  <div class="press-name" style="left:128px">Roamline</div>
  <div class="press-name" style="left:300px">Dapperly</div>
  <div class="press-name" style="left:468px;font-size:19px;top:236px">The Daily Ledger</div>
  <div class="press-name" style="left:613px">WNB</div>
  <div class="press-name" style="left:760px;font-size:21px;top:234px">Globe Juniors</div>
  <div class="press-name" style="left:920px">PRN</div>
</section>

<section class="cta paper">
  <h2 class="heading" style="top:54px;font-size:44px;color:var(--teal)">Buy Tickets Online Or</h2>
  <h2 class="heading" style="top:108px;font-size:44px;color:var(--pink)">Give Us A Call At
    <svg width="38" height="38" viewBox="0 0 24 24" style="vertical-align:-5px;margin:0 6px"><path d="M6.6 3.5 9 6.2c.4.5.4 1.2-.1 1.6L7.5 9.1c1.2 2.6 3.1 4.5 5.7 5.7l1.3-1.4c.4-.5 1.1-.5 1.6-.1l2.7 2.4c.5.4.5 1.2.1 1.7l-1.3 1.4c-.8.9-2.1 1.1-3.2.6-4.3-2-7.8-5.5-9.8-9.8-.5-1.1-.3-2.4.6-3.2l1.4-1.3c.5-.4 1.3-.4 1.7.1z" fill="none" stroke="currentColor" stroke-width="1.4"/><path d="M15 3a6 6 0 0 1 6 6M15 6a3 3 0 0 1 3 3" fill="none" stroke="currentColor" stroke-width="1.4"/></svg>
    1-800-555-0142</h2>
</section>

<footer class="footer">
  <div class="contact-box" style="left:142px">
    <svg width="40" height="40" viewBox="0 0 24 24" style="color:var(--pink)"><path d="M6.6 3.5 9 6.2c.4.5.4 1.2-.1 1.6L7.5 9.1c1.2 2.6 3.1 4.5 5.7 5.7l1.3-1.4c.4-.5 1.1-.5 1.6-.1l2.7 2.4c.5.4.5 1.2.1 1.7l-1.3 1.4c-.8.9-2.1 1.1-3.2.6-4.3-2-7.8-5.5-9.8-9.8-.5-1.1-.3-2.4.6-3.2l1.4-1.3c.5-.4 1.3-.4 1.7.1z" fill="none" stroke="currentColor" stroke-width="1.3"/><path d="M15 3a6 6 0 0 1 6 6M15 6a3 3 0 0 1 3 3" fill="none" stroke="currentColor" stroke-width="1.3"/></svg>
    <div class="label">Phone</div>
    <div class="value">123.555.0199</div>
  </div>
  <div class="abs" style="left:538px;top:62px;width:124px;height:124px;border-radius:50%;background:var(--pink)"></div>
  <div class="abs" style="left:0;width:1200px;top:200px;text-align:center;font-family:'Playfair Display',serif;font-size:36px;font-weight:700;color:var(--pink);white-space:nowrap">Neon Drifters</div>
  <div class="btn" style="left:543px;top:298px;width:114px;height:38px;background:transparent;border:1px solid #777">Book Now</div>
  <div class="contact-box" style="left:845px">
    <svg width="44" height="40" viewBox="0 0 24 22" style="color:var(--pink)"><path d="M2 9l10-7 10 7v11H2z M2 9l10 7 10-7 M6 6V3h12v3" fill="none" stroke="currentColor" stroke-width="1.2"/><path d="M8 7h8M8 9.5h8" stroke="currentColor" stroke-width="1"/></svg>
    <div class="label">Email</div>
    <div class="value" style="font-size:13px">inquiry@neondrifters.com</div>
  </div>
  <div class="abs" style="left:142px;top:356px;width:917px;height:1px;background:#333"></div>
  <div class="abs" style="left:143px;top:376px;font-size:13px;color:#ccc">© 2021 <span style="color:#fff">Neon Drifters Walking Tour.</span> All Rights Reserved.</div>
  <div class="social" style="left:893px"></div>
  <div class="social" style="left:937px"></div>
  <div class="social" style="left:981px"></div>
  <div class="social" style="left:1023px"></div>
</footer>

</body>
</html>
```